Building company buisness cards

We are looking for a sharp modern new look for our business cards.
We are a New Zealand based company that specialises in house and land packages.
We have attached a photo of the current logo and would like to see if it can be improved somehow if needed.
We are open to any colours but we have chosen green at this stage.
Feel free to change the font and make the logo smarter looking.
Play with the colours and see what looks best.

We want a card that looks so good know one will want to throw it away!

Target Market(s)

Home buyers

Industry/Entity Type

Building

Contact Information for Business Card

Derek Tolvane
0217394062
dtolvane@quillmarkhomesteads.co.nz
quillmarkhomesteads.co.nz

Font styles to use
Serif
Sans Serif

Colors

Designer to choose colors to be used in the design.

Requirements
Must have
• Logo and company name on one side, details on the other side
Nice to have
• Color codes for the original green are HEX #4a8028, RGB(74,128,40), CMYK(42,0,69,50)
• Round corners, Raised and/or spot UV

```html
<!DOCTYPE html>
<html lang="en">
<head>
<meta charset="utf-8">
<title>Quillmark Homesteads – Business Cards</title>
<link rel="stylesheet" href="https://fonts.googleapis.com/css2?family=Roboto:wght@300;400&display=swap">
<style>
  :root {
    --bg: #333333;
    --card-white: #ffffff;
    --band-dark: #0b0b0b;
    --band-mid: #2a2a2a;
    --brand-green: #238b22;
    --text-light: #e6e6e6;
    --rule-grey: #c8c8c8;
  }
  html, body {
    margin: 0;
    padding: 0;
    width: 1200px;
    height: 1200px;
    overflow: hidden;
    background: var(--bg);
    font-family: "Roboto", Arial, sans-serif;
  }
  .canvas {
    position: relative;
    width: 1200px;
    height: 1200px;
  }
  .card {
    position: absolute;
    left: 288px;
    width: 706px;
    height: 401px;
    border-radius: 16px;
    overflow: hidden;
    background: var(--card-white);
  }
  .card--details { top: 192px; }
  .card--brand { top: 664px; }

  .brand-name {
    position: absolute;
    left: 0;
    right: 0;
    margin: 0;
    text-align: center;
    font-family: "Roboto", Arial, sans-serif;
    font-weight: 400;
    color: var(--brand-green);
    letter-spacing: 0.5px;
    line-height: 1;
  }
  .card--details .brand-name { top: 82px; font-size: 40px; }
  .card--brand .brand-name { top: 206px; font-size: 46px; }

  .contact-band {
    position: absolute;
    left: 0; right: 0; bottom: 0;
    height: 202px;
    background: linear-gradient(90deg, var(--band-dark) 0%, var(--band-mid) 100%);
  }
  .contact-name {
    position: absolute;
    right: 42px;
    top: 44px;
    margin: 0;
    font-weight: 400;
    font-size: 26px;
    line-height: 1;
    color: var(--brand-green);
  }
  .contact-list {
    list-style: none;
    margin: 0;
    padding: 0;
    position: absolute;
    right: 38px;
    top: 84px;
  }
  .contact-item {
    display: flex;
    align-items: center;
    justify-content: flex-end;
    height: 29px;
    font-weight: 300;
    font-size: 16px;
    color: var(--text-light);
  }
  .contact-icon {
    width: 14px;
    height: 14px;
    margin-left: 14px;
    fill: none;
    stroke: var(--brand-green);
    stroke-width: 1.6;
  }

  .brand-rule {
    position: absolute;
    left: 308px;
    top: 290px;
    width: 92px;
    height: 1px;
    background: var(--rule-grey);
  }
</style>
</head>
<body>
<main class="canvas">

  <section class="card card--details">
    <p class="brand-name">Quillmark Homesteads</p>
    <div class="contact-band">
      <h1 class="contact-name">Derek Tolvane</h1>
      <ul class="contact-list">
        <li class="contact-item">0217394062
          <svg class="contact-icon" viewBox="0 0 16 16" aria-hidden="true"><path d="M4 2l2.5 3-1.5 1.5c1 2 2.5 3.5 4.5 4.5L11 9.5l3 2.5-1.5 2c-5 0-10-5-10-10z"/></svg>
        </li>
        <li class="contact-item">dtolvane@quillmarkhomesteads.co.nz
          <svg class="contact-icon" viewBox="0 0 16 16" aria-hidden="true"><rect x="2" y="4" width="12" height="8"/><path d="M2 4l6 5 6-5"/></svg>
        </li>
        <li class="contact-item">quillmarkhomesteads.co.nz
          <svg class="contact-icon" viewBox="0 0 16 16" aria-hidden="true"><circle cx="8" cy="8" r="6"/><ellipse cx="8" cy="8" rx="2.6" ry="6"/><path d="M2 8h12"/></svg>
        </li>
      </ul>
    </div>
  </section>

  <section class="card card--brand">
    <p class="brand-name">Quillmark Homesteads</p>
    <div class="brand-rule"></div>
  </section>

</main>
</body>
</html>
```